Blogcraft Design Project

NOTICE TO DESIGNERS
****************NOTE: PLEASE DO NOT SUBMIT ANY MORE DESIGNS, THANK YOU!!!!****************
The name of our business is Handset Review Guild and we are setting up a website to review new phones/tablets in the marketplace.
We require a 5 page design, the idea behind the project can be understood better if you visit this websites
1) ravoluna.com
2) http://plvx.com/reviews/cellphones/
Pages required are;
1) Home page which lists all the current top devices
2) A single device page that shows the device with its current specs
3) Comparison page - where 2 or 3 devices are being compared in terms of specs
4) Archive page that shows all the current videos and text reviews
5) Single post page for the device being reviewed with all its pictures, written review, video with sidebar on the side showing other reviews available.
I am opened to a nice color scheme, including red, blue and orange. We do not have any logo at the moment. Thanks
Updates
This is a notice to all designers, I have found the designer I want to work with please do not submit any more designs for now. Thank you
Industry/Entity Type
Business
Look and feel
Each slider illustrates characteristics of the customer's brand and the style your logo design should communicate.

```html
<!DOCTYPE html>
<html lang="en">
<head>
<meta charset="utf-8">
<title>Handset Review Guild</title>
<link href="https://fonts.googleapis.com/css2?family=Source+Sans+3:wght@300;400;600;700&display=swap" rel="stylesheet">
<style>
:root{
  --red:#d8151d;
  --red-dark:#b40f16;
  --blue:#0f3ea3;
  --navy:#1b2c86;
  --orange:#f47c17;
  --text:#555;
  --muted:#8a8a8a;
  --line:#dcdcdc;
  --footer:#2c2c2c;
}
*{box-sizing:border-box;margin:0;padding:0}
html,body{width:838px;height:1200px;overflow:hidden;background:#fff}
body{font-family:"Source Sans 3",sans-serif;color:var(--text);position:relative}
.abs{position:absolute}

/* header */
.site-header{position:absolute;left:0;top:0;width:838px;height:90px;background:linear-gradient(#e0161e,#c9121a)}
.brand{position:absolute;left:54px;top:17px;display:flex;align-items:center;gap:8px;color:#fff}
.brand-mark{width:30px;height:30px;background:#fff;border-radius:4px}
.brand-name{font-size:21px;line-height:22px;font-weight:400}
.search{position:absolute;left:612px;top:14px;width:178px;height:21px;background:#fff;border-radius:11px;font-size:9px;color:#999;padding:5px 10px}
.search svg{position:absolute;right:8px;top:4px}
.main-nav{position:absolute;left:334px;top:56px;display:flex;font-size:15px;color:#fff}
.main-nav a{color:#fff;text-decoration:none;padding:0 12px;border-right:1px solid rgba(0,0,0,.18);line-height:20px}
.main-nav a:last-child{border-right:none}
.btn-signup,.btn-login{position:absolute;top:52px;height:24px;font-size:12px;color:#fff;text-align:center;line-height:24px;border-radius:2px}
.btn-signup{left:670px;width:63px;background:#ee4a4f}
.btn-login{left:740px;width:56px;background:var(--red-dark);border:1px solid #8f0b10}

/* hero */
.hero{position:absolute;left:0;top:90px;width:838px;height:282px;background:linear-gradient(#e9e9e9,#fdfdfd 45%,#f2f2f2);border-bottom:1px solid #e2e2e2}
.hero-kicker{position:absolute;left:67px;top:58px;font-size:28px;font-weight:300;color:var(--red)}
.hero-title{position:absolute;left:66px;top:84px;font-size:35px;font-weight:700;color:var(--navy)}
.hero-text{position:absolute;left:68px;top:124px;width:290px;font-size:10.5px;line-height:15px;color:#888;font-weight:300}
.btn-read{position:absolute;left:66px;top:164px;width:88px;height:24px;background:var(--orange);color:#fff;font-size:11px;line-height:24px;text-align:center;border-radius:2px}
.dots{position:absolute;left:68px;top:209px;display:flex;gap:2px}
.dots i{width:9px;height:9px;border-radius:50%;background:#aaa}
.dots i:first-child{background:#111}
.hero-media{position:absolute;left:360px;top:34px;width:440px;height:224px;border-radius:18px;background:linear-gradient(135deg,#2a2a2e,#111 40%,#3a2f7a 60%,#1a1a1a);transform:skewY(-6deg)}

/* sidebar */
.panel{position:absolute;border:1px solid #e3e3e3;border-radius:3px;background:#fff}
.panel-head{height:34px;color:#fff;font-size:15px;padding:6px 18px;font-weight:600}
.companies{left:38px;top:390px;width:164px;height:408px}
.companies .panel-head{background:linear-gradient(#1a4fc0,var(--blue));font-weight:600}
.company-list{list-style:none;margin:12px 20px 0 18px}
.company-list li{font-size:10px;height:24.5px;line-height:21px;border-bottom:1px solid var(--line);color:#555}
.company-list li:last-child{border-bottom:none}
.blog{left:37px;top:812px;width:163px;height:256px}
.blog .panel-head{height:30px;background:var(--orange);padding-top:5px;font-weight:400}
.blog-item{margin:12px 14px 0 18px}
.blog-item h4{font-size:11px;font-weight:400;color:#222;margin-bottom:2px}
.blog-item p{font-size:8px;line-height:13px;color:#777}

/* products */
.section-title{position:absolute;font-size:22px;font-weight:400}
.popular-title{left:221px;top:392px;color:var(--orange)}
.reviews-title{left:220px;top:643px;color:var(--red)}
.product{position:absolute;top:428px;width:141px;height:188px;border:1px solid #e2e2e2;background:linear-gradient(#fff,#f4f4f4)}
.product .media{position:absolute;left:30px;top:14px;width:80px;height:96px;border-radius:6px}
.product h3{position:absolute;left:13px;top:118px;font-size:13px;font-weight:400;color:#333}
.product p{position:absolute;left:13px;top:136px;width:118px;font-size:8px;line-height:12px;color:#888}
.product .price{position:absolute;left:13px;top:162px;font-size:8.5px;color:#888}
.product .price b{font-size:12px;font-weight:300}

/* reviews */
.review{position:absolute;width:300px;height:110px}
.review .frame{position:absolute;left:0;top:0;width:120px;height:108px;border:1px solid #ddd;background:#fff}
.review .media{position:absolute;left:30px;top:10px;width:60px;height:88px;border-radius:6px}
.review .media.wide{left:12px;top:24px;width:96px;height:58px}
.review h3{position:absolute;left:129px;top:-3px;font-size:13.5px;font-weight:600;color:var(--navy)}
.review p{position:absolute;left:129px;top:20px;width:152px;font-size:8.6px;line-height:16.3px;color:#888}
.review .price{position:absolute;left:130px;top:87px;font-size:13px;color:var(--blue);font-weight:300}
.review .btn-more{position:absolute;left:198px;top:88px;width:61px;height:20px;background:var(--red);color:#fff;font-size:9px;line-height:20px;text-align:center;border-radius:2px}

.ph-dark{background:linear-gradient(160deg,#2c3a5c,#111827)}
.ph-light{background:linear-gradient(160deg,#e9edf2,#b7c1cc)}
.ph-tab{background:linear-gradient(160deg,#1f2a44,#4f6fb5 55%,#222)}

/* footer */
.site-footer{position:absolute;left:0;top:1108px;width:838px;height:92px;background:var(--footer);color:#fff}
.footer-nav{position:absolute;left:46px;top:24px;font-size:11px}
.footer-nav span{color:#bbb;margin:0 3px}
.copyright{position:absolute;left:46px;top:46px;font-size:9px;color:#999}
.social{position:absolute;left:688px;top:18px;display:flex;gap:1px}
.social i{width:24px;height:24px;border-radius:50%;background:#fff;display:block}
</style>
</head>
<body>

<header class="site-header">
  <div class="brand"><span class="brand-mark"></span><span class="brand-name">Handset Review<br>Guild</span></div>
  <div class="search">Search here
    <svg width="12" height="12" viewBox="0 0 12 12"><circle cx="5" cy="5" r="4" fill="none" stroke="#777" stroke-width="1.3"/><line x1="8" y1="8" x2="11" y2="11" stroke="#777" stroke-width="1.4"/></svg>
  </div>
  <nav class="main-nav"><a>Home</a><a>About Us</a><a>Latest Reviews</a><a>Compare</a></nav>
  <div class="btn-signup">Sign Up</div>
  <div class="btn-login">Log In</div>
</header>

<section class="hero">
  <div class="hero-kicker">Market Review of Latest</div>
  <div class="hero-title">Phones/Tablets</div>
  <p class="hero-text">Mauris vel lacus vitae felis vestibulum volutpat. Etiam est nunc, venenatis in, tristique eu, imperdiet ac, nisl.</p>
  <div class="btn-read">READ MORE</div>
  <div class="dots"><i></i><i></i><i></i><i></i></div>
  <div class="hero-media" role="img" aria-label="Black tablet showing a colourful tiled start screen"></div>
</section>

<aside class="panel companies">
  <div class="panel-head">Top Companies</div>
  <ul class="company-list">
    <li>Mauris vel lacus</li><li>Vitae felis</li><li>Aestibulum volut</li><li>Etiam est nunc</li>
    <li>Venenatis in</li><li>Tristique eu</li><li>Imperdiet nisl</li><li>Cum sociis</li>
    <li>Natoque</li><li>Penatibus et</li><li>Magnis dis</li><li>Mauris vel lacus</li>
    <li>Vitae felis</li><li>Vestibulum</li>
  </ul>
</aside>

<aside class="panel blog">
  <div class="panel-head">Recent Blog</div>
  <div class="blog-item"><h4>Mobile Name</h4><p>Phasellus felis dolor, scelerisque a, tempus eget, lobortis id, libero.</p></div>
  <div class="blog-item"><h4>Mobile Name</h4><p>Phasellus felis dolor, scelerisque a, tempus eget, lobortis id, libero.</p></div>
  <div class="blog-item"><h4>Mobile Name</h4><p>Nunc tempus felis vitae urna. Vivamus porttitor, g, purus nisi eleifend libero, a tempus libero us feugiat felis.</p></div>
</aside>

<h2 class="section-title popular-title">Popular Products</h2>

<article class="product" style="left:221px"><div class="media ph-dark" role="img" aria-label="Blue smartphone"></div><h3>Product Name</h3><p>Duis tincidunt lectus quis dui viverra vestibulum</p><div class="price">as low as <b>$299</b></div></article>
<article class="product" style="left:367px"><div class="media ph-dark" role="img" aria-label="Two black smartphones, front and back"></div><h3>Product Name</h3><p>Duis tincidunt lectus quis dui viverra vestibulum</p><div class="price">as low as <b>$299</b></div></article>
<article class="product" style="left:513px"><div class="media ph-dark" role="img" aria-label="Black smartphone at an angle"></div><h3>Product Name</h3><p>Duis tincidunt lectus quis dui viverra vestibulum</p><div class="price">as low as <b>$299</b></div></article>
<article class="product" style="left:658px"><div class="media ph-tab" style="left:14px;top:22px;width:112px;height:76px" role="img" aria-label="Tablet with tiled screen"></div><h3>Product Name</h3><p>Duis tincidunt lectus quis dui viverra vestibulum</p><div class="price">as low as <b>$299</b></div></article>

<h2 class="section-title reviews-title">Recent Reviews</h2>

<article class="review" style="left:219px;top:682px"><div class="frame"><div class="media ph-light" role="img" aria-label="White smartphone"></div></div><h3>Product Name</h3><p>Nunc tempus felis vitae urna. Viva-mus porttitor, g, purus nisi eleifend libero, a tempus libero lectus feugiat felis. Morbi diam mauris</p><div class="price">Price &nbsp;$199</div><div class="btn-more">Read More</div></article>
<article class="review" style="left:517px;top:682px"><div class="frame"><div class="media wide ph-tab" role="img" aria-label="Tablet with stylus"></div></div><h3 style="left:125px">Product Name</h3><p style="left:125px">Nunc tempus felis vitae urna. Viva-mus porttitor, g, purus nisi eleifend libero, a tempus libero lectus feugiat felis. Morbi diam mauris</p><div class="price" style="left:126px">Price &nbsp;$199</div><div class="btn-more" style="left:194px">Read More</div></article>

<article class="review" style="left:220px;top:819px"><div class="frame"><div class="media ph-dark" role="img" aria-label="Black smartphone with app icons"></div></div><h3>Product Name</h3><p>Nunc tempus felis vitae urna. Viva-mus porttitor, g, purus nisi eleifend libero, a tempus libero lectus feugiat felis. Morbi diam mauris</p><div class="price">Price &nbsp;$199</div><div class="btn-more">Read More</div></article>
<article class="review" style="left:513px;top:819px"><div class="frame"><div class="media wide ph-tab" role="img" aria-label="Tablet with app screen"></div></div><h3 style="left:129px">Product Name</h3><p>Nunc tempus felis vitae urna. Viva-mus porttitor, g, purus nisi eleifend libero, a tempus libero lectus feugiat felis. Morbi diam mauris</p><div class="price">Price &nbsp;$199</div><div class="btn-more">Read More</div></article>

<article class="review" style="left:223px;top:960px"><div class="frame"><div class="media ph-dark" role="img" aria-label="Phone with physical keyboard"></div></div><h3>Product Name</h3><p>Nunc tempus felis vitae urna. Viva-mus porttitor, g, purus nisi eleifend libero, a tempus libero lectus feugiat felis. Morbi diam mauris</p><div class="price">Price &nbsp;$199</div><div class="btn-more">Read More</div></article>
<article class="review" style="left:517px;top:960px"><div class="frame"><div class="media wide ph-tab" role="img" aria-label="Tablet lying at an angle"></div></div><h3 style="left:128px">Product Name</h3><p style="left:128px">Nunc tempus felis vitae urna. Viva-mus porttitor, g, purus nisi eleifend libero, a tempus libero lectus feugiat felis. Morbi diam mauris</p><div class="price" style="left:129px">Price &nbsp;$199</div><div class="btn-more" style="left:197px">Read More</div></article>

<footer class="site-footer">
  <div class="footer-nav">Home<span>/</span>About Us<span>/</span>Latest Reviews<span>/</span>Compare</div>
  <div class="copyright">Copyright © 2013 Company Name. &nbsp;All right reserved.</div>
  <div class="social"><i></i><i></i><i></i><i></i></div>
</footer>

</body>
</html>
```